Clinic for cellulit and fat removal

Name of clinic :
Lirava
- Body & Health (this has to be written on the site.)
I need CMS for me to be able to make changes myself.
A webpage for woman searching for a solution to remove fat and cellulit.
The owner is a brazilian woman in Denmark, and want her sense of aestetic shines thru the website.
There needs to be a slide show on the landing page showing big sliding pictures, of the clinic and and the treatments.
The Cryolipolysis, is a treatment freezing fat and cellulit, and this treatment will be the Attraction of the clinic.
Needs These pages in a horisontal fasion. (written in Danish)
Lirava
Behandlinger
- Cryolipolysis
- Trimflox
- Lymfemassage
- Korathelix
- Amberline Tide
Produkter
Priser
Kontakt
Clinic
Coded - Design and coding required
5+ page

```html
<!DOCTYPE html>
<html lang="en">
<head>
<meta charset="utf-8">
<title>Lirava – Body &amp; Health</title>
<link href="https://fonts.googleapis.com/css2?family=Open+Sans:wght@400;600;700&display=swap" rel="stylesheet">
<style>
:root{
  --teal:#118089;
  --teal-dark:#0b6e77;
  --ink:#333;
  --text:#444;
  --card:#f4f4f4;
  --card-edge:#e2e2e2;
  --footer:#effafb;
  --footer-bar:#d8f1f3;
  --menu:#e6e6e6;
}
*{margin:0;padding:0;box-sizing:border-box}
html,body{width:878px;height:1200px;overflow:hidden;background:#fff}
body{position:relative;font-family:'Open Sans',sans-serif;color:var(--text)}

.site-header{position:absolute;left:0;top:0;width:878px;height:70px;background:linear-gradient(180deg,#1a939b,#0f7f88)}
.brand{position:absolute;left:72px;top:20px;font-size:22px;font-weight:600;color:#fff;letter-spacing:.5px}
.main-nav a{position:absolute;top:27px;font-size:11.5px;color:#fff;text-decoration:none}
.search-icon{position:absolute;left:671px;top:28px}
.lang{position:absolute;left:704px;top:26px;width:102px;height:19px;border-bottom:1px solid #fff;font-size:11px;color:#fff;padding-left:2px}
.lang .flag{position:absolute;right:18px;top:3px;width:11px;height:8px;background:#d62e3d}
.lang .flag::before{content:"";position:absolute;left:3px;top:0;width:2px;height:8px;background:#fff}
.lang .flag::after{content:"";position:absolute;left:0;top:3px;width:11px;height:2px;background:#fff}
.lang svg{position:absolute;right:3px;top:4px}

.dropdown{position:absolute;left:399px;top:57px;width:120px;height:131px;background:var(--menu);border-top:2px solid #fff}
.dropdown::before{content:"";position:absolute;left:16px;top:-7px;border:5px solid transparent;border-bottom-color:#fff;border-top:0}
.dropdown li{list-style:none;height:22.5px;line-height:22.5px;font-size:9.5px;color:#555;padding-left:29px;position:relative}
.dropdown li::before{content:"";position:absolute;left:16px;top:8px;border:3px solid transparent;border-left:4px solid #555;border-right:0}
.dropdown li.active{background:var(--teal);color:#fff}
.dropdown li.active::before{border-left-color:#fff}

.hero{position:absolute;left:0;top:70px;width:878px;height:360px;overflow:hidden}
.hero-bg{position:absolute;inset:0;background:linear-gradient(100deg,#e4eff0 0%,#f2f3f3 35%,#f2f3f3 70%,#e2eeef 100%)}
.hero-edge{position:absolute;left:0;top:0}
.hero-photo{position:absolute;left:118px;top:15px;width:395px;height:325px;background:radial-gradient(ellipse at 45% 45%,#e9cbb5 0%,#f3e6dc 45%,rgba(243,243,243,0) 72%)}
.hero-title{position:absolute;left:466px;top:119px;font-size:43px;line-height:1;color:var(--teal);font-weight:400;letter-spacing:-.3px}
.hero-title b{font-weight:700}
.hero-text{position:absolute;left:467px;top:175px;width:330px;font-size:11.2px;line-height:15.5px;color:var(--teal)}
.btn{position:absolute;background:var(--teal);color:#fff;font-weight:700;text-align:center;text-transform:uppercase;letter-spacing:.3px}
.hero .btn{left:468px;top:220px;width:112px;height:29px;line-height:29px;font-size:11.5px}
.arrow{position:absolute;top:276px;width:27px;height:27px}
.arrow.prev{left:713px;background:#fff}
.arrow.next{left:743px;background:var(--teal)}
.arrow svg{position:absolute;left:8px;top:7px}

.card{position:absolute;top:418px;width:235px;height:303px;background:var(--card);border-bottom:4px solid var(--card-edge)}
.card-photo{height:215px}
.card h2{font-size:19px;font-weight:700;color:var(--ink);text-align:center;line-height:22.5px;margin-top:22px;letter-spacing:.4px}
.card .btn{left:61px;top:94px;width:112px;height:29px;line-height:29px;font-size:11.5px}

.about h2{position:absolute;left:94px;top:770px;font-size:19px;font-weight:700;color:var(--teal);letter-spacing:.4px}
.about p{position:absolute;left:94px;top:804px;width:434px;font-size:9.1px;line-height:15.2px;color:#333;text-align:justify}
.about .btn{left:94px;top:884px;width:96px;height:29px;line-height:29px;font-size:11.5px}
.about-photo{position:absolute;left:571px;top:752px;width:235px;height:184px;background:linear-gradient(135deg,#dedcdc,#c9b7a8 45%,#2c2a2a 75%,#d6d4d4)}

.site-footer{position:absolute;left:0;top:955px;width:878px;height:245px}
.footer-bg{position:absolute;inset:0}
.col-title{position:absolute;top:1009px;font-size:13px;color:var(--ink)}
.quick-links li{list-style:none;position:absolute;left:116px;font-size:9px;color:#333}
.quick-links li::before{content:"";position:absolute;left:-17px;top:4px;border:3px solid transparent;border-left:3px solid #333;border-right:0}
.email-field{position:absolute;left:253px;top:1049px;width:138px;height:20px;background:#fff;border:1px solid #cfd8d9;border-radius:2px;font-size:8px;color:#333;padding:4px 0 0 10px}
.email-field svg{position:absolute;right:8px;top:5px}
.subscribe{position:absolute;left:253px;top:1075px;width:63px;height:19px;line-height:19px;background:var(--teal);color:#fff;font-size:9px;text-align:center;border-radius:2px}
.contact-line{position:absolute;left:476px;font-size:9px;line-height:15px;color:#333}
.contact-icon{position:absolute;left:457px}
.social{position:absolute;top:1051px;width:22px;height:22px;border-radius:50%;background:var(--teal)}
.social.light{background:#dcedef}
.footer-brand{position:absolute;left:654px;top:1091px;font-size:22px;font-weight:600;color:var(--teal);letter-spacing:.5px}
.copyright{position:absolute;left:0;top:1177px;width:878px;height:23px;background:var(--footer-bar);font-size:8px;color:#333;text-align:center;line-height:23px}
</style>
</head>
<body>

<header class="site-header">
  <div class="brand">LIRAVA</div>
  <nav class="main-nav">
    <a style="left:405px">Behandlinger</a>
    <a style="left:490px">Produkter</a>
    <a style="left:561px">Priser</a>
    <a style="left:612px">Kontakt</a>
  </nav>
  <svg class="search-icon" width="11" height="11" viewBox="0 0 11 11"><circle cx="4.5" cy="4.5" r="3.3" fill="none" stroke="#fff" stroke-width="1.6"/><line x1="7" y1="7" x2="10" y2="10" stroke="#fff" stroke-width="1.8"/></svg>
  <div class="lang">Danish<span class="flag"></span><svg width="7" height="5" viewBox="0 0 7 5"><path d="M1 1l2.5 2.5L6 1" fill="none" stroke="#fff" stroke-width="1.2"/></svg></div>
</header>

<section class="hero">
  <div class="hero-bg" role="img" aria-label="Soft teal and white abstract slide background"></div>
  <div class="hero-photo" role="img" aria-label="Smiling woman in white sitting with knees drawn up"></div>
  <svg class="hero-edge" width="878" height="360" viewBox="0 0 878 360"><path d="M0 338 C150 360 300 375 440 372 C600 368 760 345 878 330 L878 360 L0 360Z" fill="#fff"/></svg>
  <h1 class="hero-title">Body <b>&amp; Health</b></h1>
  <p class="hero-text">The Cryolipolysis, is a treatment freezing fat and cellulit, and this treatment will be the Attraction of the clinic.</p>
  <div class="btn">Learn More</div>
  <div class="arrow prev"><svg width="10" height="13" viewBox="0 0 10 13"><path d="M7 1L2 6.5 7 12" fill="none" stroke="#555" stroke-width="1.6"/></svg></div>
  <div class="arrow next"><svg width="10" height="13" viewBox="0 0 10 13"><path d="M3 1l5 5.5L3 12" fill="none" stroke="#fff" stroke-width="1.6"/></svg></div>
</section>

<ul class="dropdown">
  <li class="active">Cryolipolysis</li>
  <li>Trimflox</li>
  <li>Lymfemassage</li>
  <li>Korathelix</li>
  <li>Amberline Tide</li>
</ul>

<article class="card" style="left:72px">
  <div class="card-photo" role="img" aria-label="Hands pinching skin on a thigh" style="background:linear-gradient(160deg,#f2ece8,#e3c9b9 50%,#efe6e0)"></div>
  <h2>FREEZING FAT AND<br>CELLULIT</h2>
</article>
<article class="card" style="left:322px">
  <div class="card-photo" role="img" aria-label="Waist and hips with dashed contour lines" style="background:radial-gradient(ellipse at 50% 50%,#d9a17d 0%,#e6c1a7 40%,#e9f1f5 80%)"></div>
  <div class="btn">Read More</div>
  <h2>CELLULIT AND FAT<br>REMOVAL</h2>
</article>
<article class="card" style="left:571px">
  <div class="card-photo" role="img" aria-label="Therapist applying a treatment device to a woman lying on a bed" style="background:linear-gradient(135deg,#e6e6e8,#eae3df 50%,#d9dbe2)"></div>
  <h2>TREATMENTS</h2>
</article>

<section class="about">
  <h2>ABOUT US</h2>
  <p>Lorem ipsum dolor sit amet, consectetur adipiscing elit, sed do eiusmod tempor incididunt ut labore et dolore magna aliqua. Ut enim ad minim veniam, quis nostrud exercitation ullamco laboris nisi ut aliquip ex ea commodo consequat. Duis aute irure dolor in reprehenderit in voluptate velit esse cillum dolore eu fugiat nulla pariatur.</p>
  <div class="btn">Read More</div>
  <div class="about-photo" role="img" aria-label="Slim waist of a woman in black sportswear"></div>
</section>

<footer class="site-footer">
  <svg class="footer-bg" width="878" height="245" viewBox="0 0 878 245"><path d="M0 35 C200 5 420 -2 600 5 C720 10 820 22 878 35 L878 245 L0 245Z" fill="var(--footer)"/></svg>
</footer>

<div class="col-title" style="left:95px">Quick Links</div>
<div class="col-title" style="left:253px">Newsletter</div>
<div class="col-title" style="left:457px;top:1008px">Contact Us</div>
<div class="col-title" style="left:652px;top:1008px">Follow Us</div>

<ul class="quick-links">
  <li style="top:1047px">Lirava</li>
  <li style="top:1066px">Behandlinger</li>
  <li style="top:1085px">Produkter</li>
  <li style="top:1104px">Priser</li>
  <li style="top:1122px">Kontakt</li>
</ul>

<div class="email-field">Enter Email id<svg width="9" height="8" viewBox="0 0 9 8"><path d="M1 3.5L4.5 1 8 3.5V7H1Z M1 3.5L4.5 5.5 8 3.5" fill="none" stroke="#555" stroke-width=".8"/></svg></div>
<div class="subscribe">Subscribe</div>

<svg class="contact-icon" style="top:1051px" width="10" height="13" viewBox="0 0 10 13"><path d="M5 12C2 8 1 6.5 1 4.6A4 4 0 0 1 9 4.6C9 6.5 8 8 5 12Z" fill="none" stroke="#222" stroke-width="1.4"/><circle cx="5" cy="4.6" r="1.4" fill="#222"/></svg>
<div class="contact-line" style="top:1047px">Studio 12 Havnegade<br>Vest Aarhus</div>
<svg class="contact-icon" style="top:1093px" width="10" height="10" viewBox="0 0 10 10"><path d="M2 0.5L4 3 3 4.3C3.8 5.8 4.4 6.4 5.8 7.1L7 6 9.5 8 8.3 9.5C4.5 9.3 0.8 5.6 0.6 1.7Z" fill="#222"/></svg>
<div class="contact-line" style="top:1091px">(452)-718-3390</div>
<svg class="contact-icon" style="top:1117px" width="10" height="8" viewBox="0 0 10 8"><rect x=".5" y=".5" width="9" height="7" fill="#222"/><path d="M.5 .8L5 4.3 9.5 .8" fill="none" stroke="#fff" stroke-width=".9"/></svg>
<div class="contact-line" style="top:1113px">hej@liravaklinik.dk</div>

<div class="social light" style="left:652px"></div>
<div class="social" style="left:677px"></div>
<div class="social" style="left:702px"></div>
<div class="social" style="left:727px"></div>
<div class="footer-brand">LIRAVA</div>

<div class="copyright">Copyrights © 2017, www.liravaklinik.dk. All Rights Reserved.</div>

</body>
</html>
```